Bookmark Design

We would like to design a book mark with logos of our two business and a quote.

One side with the quote "The first wealth is health" - Tobias Kendrick Mallory and the two logos.

The back side has the two logos with its respective phone numbers and a common address (this is to be advised to the winner of the project).

```html
<!DOCTYPE html>
<html lang="en">
<head>
<meta charset="utf-8">
<title>Bookmark – The first wealth is health</title>
<link href="https://fonts.googleapis.com/css2?family=Montserrat:wght@500;600;700;800&display=swap" rel="stylesheet">
<style>
  :root {
    --backdrop: #e8e8e8;
    --green-light: #7cbd2a;
    --green-main: #55a83e;
    --green-deep: #48a03f;
    --leaf-tint: rgba(40, 130, 50, 0.22);
    --band-blue: #2a3a97;
    --paper: #ffffff;
    --stub: #f3f3f3;
    --ink-white: #ffffff;
    --clinic-blue: #2b3a97;
    --dental-green: #3e9a3a;
    --perforation: #c4c4c4;
  }
  * { box-sizing: border-box; margin: 0; padding: 0; }
  html, body {
    width: 1200px;
    height: 801px;
    overflow: hidden;
    background: var(--backdrop);
    font-family: "Montserrat", sans-serif;
  }
  .bookmark {
    position: absolute;
    left: 450px;
    top: 26px;
    width: 300px;
    height: 750px;
    background: var(--stub);
    box-shadow: 0 2px 8px rgba(0,0,0,0.12);
  }
  .bookmark__face {
    position: absolute;
    inset: 0 0 250px 0;
    background: linear-gradient(200deg, var(--green-light) 0%, var(--green-main) 45%, var(--green-deep) 100%);
    overflow: hidden;
  }
  .bookmark__foliage {
    position: absolute;
    right: -20px;
    top: 150px;
    width: 170px;
    height: 340px;
    border-radius: 50% 50% 40% 40%;
    background: radial-gradient(ellipse at 60% 40%, var(--leaf-tint), transparent 70%);
  }
  .bookmark__hole {
    position: absolute;
    right: 38px;
    top: 44px;
    width: 30px;
    height: 30px;
    border-radius: 50%;
    background: var(--backdrop);
    box-shadow: inset 0 1px 2px rgba(0,0,0,0.25);
  }
  .quote {
    position: absolute;
    left: 26px;
    top: 88px;
    width: 260px;
    color: var(--ink-white);
  }
  .quote__mark {
    display: block;
    font-size: 30px;
    font-weight: 700;
    line-height: 20px;
  }
  .quote__mark--open { margin-left: 4px; }
  .quote__text {
    font-size: 44px;
    font-weight: 800;
    line-height: 44px;
    letter-spacing: -1.5px;
    padding-left: 8px;
  }
  .quote__mark--close {
    display: inline-block;
    font-size: 24px;
    vertical-align: bottom;
    margin-left: 4px;
  }
  .author {
    position: absolute;
    left: 12px;
    top: 306px;
    width: 262px;
    height: 24px;
    background: var(--band-blue);
    color: var(--ink-white);
    font-size: 10.5px;
    font-weight: 600;
    letter-spacing: 1.4px;
    text-transform: uppercase;
    line-height: 24px;
    text-align: center;
  }
  .partners {
    position: absolute;
    left: 20px;
    top: 368px;
    display: flex;
    gap: 10px;
  }
  .partner {
    width: 96px;
    height: 96px;
    border-radius: 6px;
    background: var(--paper);
    display: flex;
    flex-direction: column;
    align-items: center;
    justify-content: center;
    gap: 8px;
    text-align: center;
    font-size: 12px;
    font-weight: 700;
    line-height: 14px;
  }
  .partner--dental { width: 108px; }
  .partner__dot {
    width: 22px;
    height: 22px;
    border-radius: 50%;
  }
  .partner--clinic { color: var(--clinic-blue); }
  .partner--clinic .partner__dot { background: var(--clinic-blue); }
  .partner--dental { color: var(--dental-green); }
  .partner--dental .partner__dot { background: var(--dental-green); }
  .bookmark__stub {
    position: absolute;
    left: 0;
    right: 0;
    bottom: 0;
    height: 250px;
    background: linear-gradient(180deg, var(--paper), var(--stub));
  }
  .bookmark__perforation {
    position: absolute;
    left: 26px;
    right: 20px;
    top: 56px;
    border-top: 2px dotted var(--perforation);
  }
</style>
</head>
<body>
  <article class="bookmark">
    <section class="bookmark__face">
      <div class="bookmark__foliage" role="img" aria-label="Faint leaf motif in darker green"></div>
      <div class="bookmark__hole"></div>
      <blockquote class="quote">
        <span class="quote__mark quote__mark--open">“</span>
        <p class="quote__text">The first wealth is health<span class="quote__mark quote__mark--close">”</span></p>
      </blockquote>
      <p class="author">Tobias Kendrick Mallory</p>
      <div class="partners">
        <div class="partner partner--clinic">
          <span class="partner__dot"></span>
          <span class="partner__name">Larchmont<br>Clinic</span>
        </div>
        <div class="partner partner--dental">
          <span class="partner__dot"></span>
          <span class="partner__name">Brightside<br>Dental</span>
        </div>
      </div>
    </section>
    <section class="bookmark__stub">
      <div class="bookmark__perforation"></div>
    </section>
  </article>
</body>
</html>
```